VELTAR WEBSITE

need to create a new website for VELTAR ltd
the company deals with all aspects of safety products & safety wear
we need a simple website to show
ideas can be taken from following website whose products we shall distribute in kenya
www.kwr.co.uk
www.dorvik.eu
www.brimtoolsupplyco.com
www.gardvalewerks.co.za

we need following tabs
1) home - basic company information
2) products - broken down to following categories ie gloves, head protection, ear protection, mouth protection, foot protection
3) contacts

the company profile is a reputable company dealing with all aspects of safety, HSE (health and safety equipment), and PPE (personal protective equipment)

the website should have the dorvik logo for which we are an authorized distributor.
the dorvi industrial range writeup can be picked from their website
Updates

Dear Designers, i shall be able to choose a final design in 2 weeks, sorry i have not been able to finalise this due to a personal reason

Target Market(s)

the buyers are all types of industry who care for their employees safety

Industry/Entity Type

Industrial

Requirements
Must have
• clean look, fresh look, user freindly
Nice to have
• clear images, quick links etc

```html
<!DOCTYPE html>
<html lang="en">
<head>
<meta charset="utf-8">
<title>VELTAR – Safety Gear Specialists</title>
<link href="https://fonts.googleapis.com/css2?family=Lato:wght@400;700;900&family=Open+Sans:wght@400;700;800&display=swap" rel="stylesheet">
<style>
:root{
  --yellow:#ffc600;
  --dark:#333333;
  --footer:#3a3a3a;
  --line:#e6e6e6;
  --grey-panel:#dedede;
  --muted:#9b9b9b;
  --text:#444;
}
*{margin:0;padding:0;box-sizing:border-box}
html,body{width:1088px;height:1200px;overflow:hidden;background:#fff}
.stage{position:absolute;left:0;top:0;width:1190px;height:1323px;transform:scale(.907);transform-origin:0 0;font-family:"Lato",sans-serif;color:var(--dark)}
.abs{position:absolute}
.header{left:169px;top:24px;width:853px;height:84px;background:var(--yellow)}
.logo{left:218px;top:24px;width:167px;height:84px;background:#fffbe8;display:flex;align-items:center;justify-content:center;gap:10px;font-weight:900;font-size:24px;letter-spacing:1px;color:var(--dark);box-shadow:0 2px 4px rgba(0,0,0,.08)}
.logo .mark{width:18px;height:18px;background:var(--dark);border-radius:50%}
.nav a{position:absolute;top:58px;font-size:15px;font-weight:700;color:var(--dark);text-decoration:none;letter-spacing:-.3px}
.nav .active-bar{position:absolute;left:675px;top:24px;width:70px;height:3px;background:#fff}
.page{left:169px;top:108px;width:853px;height:895px;border-left:1px solid var(--line);border-right:1px solid var(--line)}
.tag{left:218px;top:137px;width:167px;height:20px;background:var(--dark);border-top:4px solid var(--yellow);color:var(--yellow);font:800 8px/8px "Open Sans",sans-serif;padding:0 0 0 7px;letter-spacing:.6px;white-space:nowrap;overflow:hidden}
.headline{left:218px;top:214px;font:800 42px/41px "Open Sans",sans-serif;color:var(--dark);letter-spacing:-.5px}
.headline .accent{color:var(--yellow)}
.btn-offers{left:219px;top:365px;width:135px;height:32px;background:var(--dark);color:#fff;font:700 17px/32px "Lato",sans-serif;text-align:center;letter-spacing:.5px;box-shadow:0 1px 2px rgba(0,0,0,.4)}
.hero-photo{left:570px;top:145px;width:400px;height:288px;background:radial-gradient(ellipse 45% 60% at 55% 55%,#eadf6a 0%,#d8cf78 40%,#b59b7a 70%,#fff 100%)}
.dots span{position:absolute;top:135px;width:8px;height:8px;border-radius:50%;background:var(--yellow)}
.hline{height:1px;background:var(--line)}
.section-title{font:700 17px "Lato",sans-serif;color:var(--dark)}
.products-head{left:737px;top:433px;width:285px;height:87px;background:var(--yellow);display:flex;align-items:center;padding-left:42px;gap:19px;font:700 18px "Lato",sans-serif}
.search-ico{width:25px;height:25px;background:var(--dark);display:flex;align-items:center;justify-content:center}
.vline{left:737px;width:1px;background:var(--line)}
.body-copy{left:219px;top:542px;width:476px;font:400 11px/17px "Open Sans",sans-serif;color:var(--text);letter-spacing:.55px}
.body-copy p{margin-bottom:17px}
.btn-small{height:20px;font:400 11px/20px "Lato",sans-serif;text-align:center;text-transform:uppercase}
.btn-dark{background:var(--dark);color:#fff}
.btn-yellow{background:var(--yellow);color:var(--dark)}
.cat-list{left:779px;top:546px;list-style:none}
.cat-list li{display:flex;align-items:center;height:36.8px;font:400 11px "Open Sans",sans-serif;letter-spacing:1px;color:var(--dark)}
.cat-list .plus{width:25px;height:24px;background:var(--dark);color:#fff;display:flex;align-items:center;justify-content:center;font-size:15px;margin-right:22px}
.partner{left:737px;top:782px;width:285px;height:87px;background:var(--grey-panel);display:flex;flex-direction:column;align-items:center;justify-content:center;color:#9a9a9a}
.partner .name{font:700 24px/24px "Lato",sans-serif}
.partner .sub{font:700 7px "Lato",sans-serif;letter-spacing:.3px;margin-top:4px}
.cat-strip{left:169px;top:869px;width:853px;height:31px;background:var(--yellow);display:flex}
.cat-strip div{flex:1;font:700 11.5px/31px "Lato",sans-serif;text-align:center;border-right:1px solid rgba(0,0,0,.08)}
.sellers{left:169px;top:900px;width:853px;height:103px;display:flex}
.sellers .cell{flex:1;border-right:1px solid var(--line);display:flex;align-items:center;justify-content:center}
.sellers .thumb{width:62px;height:78px;border-radius:10px}
.footer{left:169px;top:1003px;width:854px;height:270px;background:repeating-linear-gradient(135deg,#3c3c3c 0 2px,#363636 2px 4px)}
.foot-col{top:1036px;width:220px;color:#c8c8c8}
.foot-col h3{font:400 17px "Lato",sans-serif;color:#cfcfcf;height:52px;border-bottom:1px solid #2a2a2a}
.foot-col ul{list-style:none;border-top:1px solid #4a4a4a;border-bottom:1px solid #2a2a2a;padding:9px 0 6px;height:100px}
.foot-col li{font:400 13px/21px "Lato",sans-serif;letter-spacing:.5px;color:#bdbdbd;white-space:nowrap}
.foot-rule{border-top:1px solid #4a4a4a}
.social{position:absolute;top:1122px;width:35px;height:35px;border-radius:50%;background:#262626;display:flex;align-items:center;justify-content:center}
.foot-brand{top:1204px;font:700 11px "Lato",sans-serif;color:#6e6e6e;text-align:center}
.foot-brand .big{font-size:19px;display:block;line-height:20px}
.foot-brand .small{font-size:6px;letter-spacing:1.5px;font-weight:400}
.copyright{left:169px;top:1292px;width:853px;text-align:center;font:400 10px "Lato",sans-serif;color:#555}
.fade{left:169px;top:1273px;width:854px;height:50px;background:linear-gradient(#e8e8e8,#fff)}
</style>
</head>
<body>
<div class="stage">
  <div class="abs page"></div>
  <div class="abs header"></div>
  <div class="abs logo"><span class="mark"></span>VELTAR</div>
  <nav class="nav">
    <span class="active-bar"></span>
    <a href="#" style="left:687px">HOME</a>
    <a href="#" style="left:779px">PRODUCTS</a>
    <a href="#" style="left:905px">CONTACT</a>
  </nav>

  <div class="abs tag">SPECIALIZED PROTECTIVE<br>&amp; INDUSTRIAL PRODUCTS</div>
  <h1 class="abs headline">BETTER<br>PROTECTION<br><span class="accent">BETTER VALUE</span></h1>
  <div class="abs btn-offers">VIEW OFFERS</div>
  <div class="abs hero-photo" role="img" aria-label="Photo of a worker in a yellow hard hat, safety glasses and hi-vis vest"></div>
  <div class="dots"><span style="left:936px"></span><span style="left:951px"></span><span style="left:966px"></span></div>

  <div class="abs hline" style="left:169px;top:433px;width:853px"></div>
  <h2 class="abs section-title" style="left:219px;top:468px">KENYA’S SAFTEY GEAR SPECIALISTS</h2>
  <div class="abs products-head">
    <span class="search-ico"><svg width="14" height="14" viewBox="0 0 14 14"><circle cx="6" cy="6" r="4.3" fill="none" stroke="#fff" stroke-width="2"/><line x1="9" y1="9" x2="13" y2="13" stroke="#fff" stroke-width="2.4"/></svg></span>
    PRODUCTS
  </div>
  <div class="abs hline" style="left:169px;top:520px;width:568px"></div>
  <div class="abs vline" style="top:520px;height:262px"></div>

  <div class="abs body-copy">
    <p>Duis fringilla dapibus justo, ut congue ligula venenatis sed. In euismod risus eget mi vestibulum a interdum sem commodo. Ut felis et massa sot.</p>
    <p>Quisque ultricies leo id felis porttitor eu sagittis orci imperdiet. Nulla vitae odio quis massa condimentum venenatis. Ut fermentum felis et massa sodales sit amet auctor urna pulvinar. In faucibus neque egestas ipsum lacinia lacinia.</p>
    <p>Quisque ultricies leo id felis porttitor eu sagittis orci imperdiet. Nulla vitae odio quis massa condimentum venenatis. Ut fermentum felis et massa sodales.</p>
  </div>
  <div class="abs btn-small btn-dark" style="left:219px;top:727px;width:86px">Read more</div>

  <ul class="abs cat-list">
    <li><span class="plus">+</span>GLOVES</li>
    <li><span class="plus">+</span>HEAD PROTECTION</li>
    <li><span class="plus">+</span>EAR PROTECTION</li>
    <li><span class="plus">+</span>MOUTH PROTECTION</li>
    <li><span class="plus">+</span>FOOT PROTECTION</li>
    <li><span class="plus">+</span>EYE PROTECTION</li>
  </ul>

  <div class="abs hline" style="left:169px;top:782px;width:568px"></div>
  <h2 class="abs section-title" style="left:219px;top:816px">TOP SELLERS</h2>
  <div class="abs partner"><span class="name">Dorvik</span><span class="sub">AUTHORIZED DISTRIBUTOR</span></div>

  <div class="abs cat-strip">
    <div>GLOVES</div><div>HEAD PROTECTION</div><div>EAR PROTECTION</div><div>MOUTH PROTECTION</div><div>FOOT PROTECTION</div><div style="border:0">EYE PROTECTION</div>
  </div>
  <div class="abs sellers">
    <div class="cell"><div class="thumb" role="img" aria-label="Product photo: work gloves" style="background:linear-gradient(#e8a21a,#3a3a3a)"></div></div>
    <div class="cell"><div class="thumb" role="img" aria-label="Product photo: welding helmet" style="background:linear-gradient(#555,#222)"></div></div>
    <div class="cell"><div class="thumb" role="img" aria-label="Product photo: ear defenders" style="background:linear-gradient(#2d2d2d,#e9b400)"></div></div>
    <div class="cell"><div class="thumb" role="img" aria-label="Product photo: respirator mask" style="background:linear-gradient(#777,#c9b03a)"></div></div>
    <div class="cell"><div class="thumb" role="img" aria-label="Product photo: safety boot" style="background:linear-gradient(#444,#1c1c1c)"></div></div>
    <div class="cell" style="border:0"><div class="thumb" role="img" aria-label="Product photo: face shield" style="background:linear-gradient(#ffd23a,#e8eef0)"></div></div>
  </div>

  <footer>
    <div class="abs footer"></div>
    <div class="abs foot-col" style="left:217px">
      <h3>CUSTOMER SERVICES</h3>
      <ul><li>Our Distribution</li><li>Useful Links</li><li>Advanced Search</li><li>Knowledge Base</li></ul>
      <div class="foot-rule"></div>
    </div>
    <div class="abs btn-small btn-yellow" style="left:217px;top:1219px;width:86px">Read more</div>

    <div class="abs foot-col" style="left:486px">
      <h3>CONTACT</h3>
      <ul><li>48 Kilima Road</li><li>Nairobi, KE 00418</li><li>E -mail: info@veltar.com</li><li>Telephone: +1 800 555 0142</li></ul>
      <div class="foot-rule"></div>
    </div>
    <div class="abs btn-small btn-yellow" style="left:486px;top:1219px;width:86px">Contact us</div>

    <div class="abs foot-col" style="left:757px">
      <h3>SHARE</h3>
      <ul></ul>
      <div class="foot-rule"></div>
    </div>
    <span class="social" style="left:769px" aria-label="Share on social network"></span>
    <span class="social" style="left:844px" aria-label="Share on social network"></span>
    <span class="social" style="left:919px" aria-label="Share by email"><svg width="17" height="12" viewBox="0 0 17 12"><rect width="17" height="12" rx="1.5" fill="#9a9a9a"/><path d="M1 1.5 8.5 7 16 1.5" fill="none" stroke="#262626" stroke-width="1.5"/></svg></span>
    <div class="abs foot-brand" style="left:754px;width:120px"><span class="big">Dorvik</span><span class="small">AUTHORIZED DISTRIBUTOR</span></div>
    <div class="abs foot-brand" style="left:900px;width:72px;top:1222px;font-size:13px;letter-spacing:1px">VELTAR</div>
  </footer>

  <div class="abs fade"></div>
  <div class="abs copyright">© &nbsp;2013 - Veltar</div>
</div>
</body>
</html>
```